Homemaking training schools needs a Business Card design

Designer, Hello!

No special requirements, good-looking enough.
--------------------------------------------------------------------------

Name: Marcus Dole
Chairman
Tel: 0574-71948263
Mobile: 13857420916
Email: kelvora@mailnest.example
Web: www.prt2019.example
Add: No.258, LanpingJie, BeiyuanQu, Ningbo, Zhejiang

LOGO
Ningbo PRT Homemaking Training School

Target Market(s)

pregnant women, mothers, infants, the elderly and families, including cleaning, cooking, nursing training.

Industry/Entity Type

Business

Contact Information for Business Card

Name: Marcus Dole
Chairman
Tel: 0574-71948263
Mobile: 13857420916
Email: kelvora@mailnest.example
Web: www.prt2019.example

LOGO

Font styles to use
Serif
Sans Serif
Decorative

Requirements
Nice to have
• Feels: clean, specifications, safety, comfort, warmth and happiness.

```html
<!DOCTYPE html>
<html lang="en">
<head>
<meta charset="utf-8">
<title>Pingrui Tang Training &amp; Services – Business Card</title>
<link rel="stylesheet" href="https://fonts.googleapis.com/css2?family=Josefin+Sans:wght@700&family=Yellowtail&display=swap">
<style>
  :root {
    --card-mint: #73c8a9;
    --text-rust: #c8532e;
    --rule-grey: #3f4f4a;
    --ornament-white: #ffffff;
  }
  html, body {
    margin: 0;
    padding: 0;
    width: 1200px;
    height: 704px;
    overflow: hidden;
  }
  .business-card {
    position: relative;
    width: 1200px;
    height: 704px;
    background: var(--card-mint);
    overflow: hidden;
  }
  .ornament {
    position: absolute;
    left: 562px;
    width: 80px;
    height: 30px;
    background: var(--ornament-white);
    opacity: 0.9;
  }
  .ornament--top { top: 32px; }
  .ornament--bottom { top: 636px; }

  .brand-name {
    position: absolute;
    left: 0;
    width: 1200px;
    top: 270px;
    margin: 0;
    text-align: center;
    font-family: "Josefin Sans", sans-serif;
    font-weight: 700;
    font-size: 72px;
    line-height: 1;
    letter-spacing: 6px;
    text-transform: uppercase;
    color: var(--text-rust);
  }
  .tagline-row {
    position: absolute;
    left: 230px;
    width: 746px;
    top: 358px;
    height: 40px;
    display: flex;
    align-items: center;
    justify-content: space-between;
  }
  .tagline-rule {
    width: 162px;
    height: 3px;
    background: var(--rule-grey);
  }
  .tagline {
    margin: 0;
    font-family: "Josefin Sans", sans-serif;
    font-weight: 700;
    font-size: 26px;
    letter-spacing: 2px;
    text-transform: uppercase;
    color: var(--text-rust);
  }

  .holder-name {
    position: absolute;
    left: 373px;
    width: 400px;
    top: 466px;
    margin: 0;
    text-align: center;
    font-family: "Yellowtail", cursive;
    font-weight: 400;
    font-size: 74px;
    line-height: 1;
    color: var(--text-rust);
  }
  .holder-title {
    position: absolute;
    left: 404px;
    width: 400px;
    top: 543px;
    margin: 0;
    text-align: center;
    font-family: "Josefin Sans", sans-serif;
    font-weight: 700;
    font-size: 24px;
    line-height: 1;
    letter-spacing: 3px;
    text-transform: uppercase;
    color: var(--text-rust);
  }

  .contact-list {
    position: absolute;
    left: 792px;
    top: 552px;
    margin: 0;
    padding: 0;
    list-style: none;
    font-family: "Josefin Sans", sans-serif;
    font-weight: 700;
    font-size: 15.5px;
    line-height: 20px;
    letter-spacing: 1.6px;
    text-transform: uppercase;
    color: var(--text-rust);
  }
  .contact-list .contact-address {
    margin-top: 19px;
    padding-left: 54px;
    text-indent: -54px;
  }
</style>
</head>
<body>
  <main class="business-card">
    <div class="ornament ornament--top" role="img" aria-label="Small white diamond ornament"></div>

    <header class="brand">
      <h1 class="brand-name">Pingrui Tang</h1>
      <div class="tagline-row">
        <span class="tagline-rule" aria-hidden="true"></span>
        <p class="tagline">Training &amp; Services</p>
        <span class="tagline-rule" aria-hidden="true"></span>
      </div>
    </header>

    <section class="holder">
      <h2 class="holder-name">Marcus Dole</h2>
      <p class="holder-title">Chairman</p>
    </section>

    <ul class="contact-list">
      <li>Tel: 0574-71948263</li>
      <li>Mobile: 13857420916</li>
      <li>Email: kelvora@mailnest.example</li>
      <li>Web: www.prt2019.example</li>
      <li class="contact-address">Add: No.258, LanpingJie, BeiyuanQu,<br>Ningbo, Zhejiang</li>
    </ul>

    <div class="ornament ornament--bottom" role="img" aria-label="Small white diamond ornament"></div>
  </main>
</body>
</html>
```